Small Business Broker Business Card Design

A business card design for a small business brokerage, which is a financial service, not unlike real estate brokerage, but for small businesses such as laundromats, pizza shops, restaurants, cleaners etc. The designs should all be simple, more conservative in nature, using the colors and font of the logo. Again, think real estate Brokerage as a business context
Contact Information for Business Card
Name: Glen R. Harlow. Title: Small Business Advisor. Email: g.harlow@bayfieldcapitalworks.example. Mobile: (555) 274-3918. Office: (555) 806-2147. www.bayfieldcapitalworks.example

```html
<!DOCTYPE html>
<html lang="en">
<head>
<meta charset="utf-8">
<title>Bayfield Capital Works — Business Card</title>
<link rel="stylesheet" href="https://fonts.googleapis.com/css2?family=Montserrat:wght@500;600;700&family=Open+Sans:wght@400;600;700&display=swap">
<style>
  :root {
    --navy: #1b3a6b;
    --navy-deep: #17386a;
    --green: #8dc63f;
    --green-soft: #74b04f;
    --ink: #3f3f3f;
    --rule: #b9b9b9;
    --paper: #ffffff;
    --backdrop: #9a9a9a;
  }
  * { box-sizing: border-box; margin: 0; padding: 0; }
  html, body { width: 1200px; height: 1200px; overflow: hidden; }
  body { background: var(--backdrop); position: relative; font-family: "Open Sans", Arial, sans-serif; }

  .card { position: absolute; left: 226px; width: 746px; height: 436px; }

  .card-front {
    top: 141px;
    background: linear-gradient(120deg, var(--navy-deep) 0%, var(--navy-deep) 18%, #2d5a6a 52%, var(--green-soft) 100%);
    color: #fff;
    display: flex; flex-direction: column; align-items: center; justify-content: center;
    text-align: center;
  }
  .front-name {
    font-family: "Montserrat", Arial, sans-serif; font-weight: 600;
    font-size: 31px; letter-spacing: 0.6px; line-height: 1; white-space: nowrap;
  }
  .front-tagline {
    font-family: "Montserrat", Arial, sans-serif; font-weight: 600;
    font-size: 15px; letter-spacing: 2px; margin-top: 9px; white-space: nowrap;
  }

  .card-back { top: 659px; background: var(--paper); }

  .brand-block {
    position: absolute; left: 30px; width: 300px; top: 150px;
    display: flex; flex-direction: column; align-items: center;
  }
  .brand-mark { width: 38px; height: 38px; background: var(--green); margin-bottom: 16px; }
  .brand-name {
    font-family: "Montserrat", Arial, sans-serif; font-weight: 700;
    font-size: 16px; color: var(--navy); letter-spacing: 0.2px; white-space: nowrap;
  }
  .brand-tagline {
    font-family: "Montserrat", Arial, sans-serif; font-weight: 600;
    font-size: 8px; color: var(--green); letter-spacing: 1px; margin-top: 3px; white-space: nowrap;
  }

  .divider { position: absolute; left: 347px; top: 116px; width: 1px; height: 206px; background: var(--rule); }

  .contact-block { position: absolute; left: 376px; top: 150px; }
  .person-name {
    font-family: "Montserrat", Arial, sans-serif; font-weight: 700;
    font-size: 21px; color: var(--navy); letter-spacing: 0.6px; line-height: 1;
  }
  .person-title {
    font-family: "Montserrat", Arial, sans-serif; font-weight: 600;
    font-size: 13.5px; color: var(--green); letter-spacing: 0.6px; margin-top: 6px;
  }
  .contact-list { list-style: none; margin-top: 24px; font-size: 17px; color: var(--ink); line-height: 25px; }
  .contact-list .label { font-weight: 700; }

  .website {
    position: absolute; left: 0; right: 0; top: 393px; text-align: center;
    font-size: 17.5px; color: var(--ink);
  }
</style>
</head>
<body>
  <section class="card card-front" aria-label="Card front">
    <div class="front-name">BAYFIELD CAPITAL WORKS, INC</div>
    <div class="front-tagline">STEADY HELP TO BUY OR SELL A NEIGHBORHOOD SHOP</div>
  </section>

  <section class="card card-back" aria-label="Card back">
    <div class="brand-block">
      <div class="brand-mark"></div>
      <div class="brand-name">BAYFIELD CAPITAL WORKS, INC</div>
      <div class="brand-tagline">STEADY HELP TO BUY OR SELL A NEIGHBORHOOD SHOP</div>
    </div>

    <div class="divider"></div>

    <div class="contact-block">
      <div class="person-name">GLEN R. HARLOW</div>
      <div class="person-title">SMALL BUSINESS ADVISOR</div>
      <ul class="contact-list">
        <li>g.harlow@bayfieldcapitalworks.example</li>
        <li><span class="label">Mobile:</span> (555) 274-3918</li>
        <li><span class="label">Office:</span> (555) 806-2147</li>
      </ul>
    </div>

    <div class="website">www.bayfieldcapitalworks.example</div>
  </section>
</body>
</html>
```